Visitenkarten-Design für Yogakurse
Zielgruppe
Ich biete Yogakurse für alle an sowieso speziell Yogakurse für Schwangere, frischgebackene Mamas und Rückbildungskurse.
Meine Zielgruppe sind hauptsächlich schwangere Frauen sowieso Frauen mit Babys.
Aufgabenstellung
Folgende Informationen sollten enthalten sein:
Stille im Atem
Yoga & Beckenbodentraining
Henrike Mollberg
info@stille-im-atem.de
www.stille-im-atem.de

```html
<!DOCTYPE html>
<html lang="de">
<head>
<meta charset="utf-8">
<title>Stille im Atem – Visitenkarte</title>
<link rel="stylesheet" href="https://fonts.googleapis.com/css2?family=Open+Sans:wght@400;500&display=swap">
<style>
  :root {
    --canvas: #e6e6e4;
    --card-white: #f6f6f4;
    --card-black: #121212;
    --gold: #c79a45;
    --gold-deep: #a97f3a;
    --sage: #c6dcb4;
    --taupe: #ad8f7e;
  }
  * { margin: 0; padding: 0; box-sizing: border-box; }
  html, body { width: 1200px; height: 800px; overflow: hidden; }
  body {
    background: var(--canvas);
    font-family: "Open Sans", Arial, sans-serif;
    position: relative;
  }
  .card {
    position: absolute;
    top: 264px;
    width: 480px;
    height: 272px;
    overflow: hidden;
    box-shadow: 0 1px 3px rgba(0,0,0,0.15);
  }
  .card--front { left: 90px; background: var(--card-black); }
  .card--back { left: 630px; background: var(--card-white); }
  .card__art { position: absolute; inset: 0; width: 100%; height: 100%; }

  .front__brand {
    position: absolute;
    left: 0; right: 0; top: 82px;
    text-align: center;
    font-size: 22px;
    font-weight: 500;
    color: var(--gold);
  }
  .front__rule {
    position: absolute;
    left: 118px; width: 244px; top: 143px;
    height: 1px;
    background: var(--sage);
  }
  .front__offer {
    position: absolute;
    left: 0; right: 0; top: 150px;
    text-align: center;
    font-size: 16px;
    line-height: 25px;
    color: var(--gold);
  }

  .back__person {
    position: absolute;
    left: 33px; top: 62px;
  }
  .back__name {
    font-size: 20px;
    font-weight: 400;
    color: var(--taupe);
    line-height: 1.1;
  }
  .back__role {
    font-size: 9px;
    color: var(--taupe);
    margin-top: 1px;
  }
  .back__rule {
    width: 24px; height: 1px;
    background: var(--sage);
    margin-top: 5px;
  }
  .contact-list {
    position: absolute;
    left: 32px; top: 116px;
    list-style: none;
  }
  .contact-list__item {
    display: flex;
    align-items: center;
    height: 25px;
    margin-bottom: 11px;
    font-size: 9.5px;
    color: var(--taupe);
    letter-spacing: 0.2px;
  }
  .contact-list__icon {
    width: 25px; height: 25px;
    border-radius: 50%;
    background: var(--sage);
    display: flex; align-items: center; justify-content: center;
    margin-right: 8px;
    flex-shrink: 0;
  }
  .contact-list__icon svg { width: 12px; height: 12px; fill: var(--gold-deep); }
  .back__brand {
    position: absolute;
    left: 318px; width: 158px;
    top: 176px;
    text-align: center;
    font-size: 20px;
    font-weight: 500;
    color: var(--gold);
    white-space: nowrap;
  }
</style>
</head>
<body>

<section class="card card--front" aria-label="Visitenkarte Vorderseite">
  <svg class="card__art" viewBox="0 0 480 272" aria-hidden="true">
    <ellipse cx="238" cy="138" rx="150" ry="176" fill="none" stroke="#c79a45" stroke-width="2"/>
    <ellipse cx="238" cy="138" rx="142" ry="170" fill="#f6f6f4"/>
  </svg>
  <p class="front__brand">Stille im Atem</p>
  <div class="front__rule"></div>
  <p class="front__offer">Yoga<br>&amp;<br>Beckenbodentraining</p>
</section>

<section class="card card--back" aria-label="Visitenkarte Rückseite">
  <svg class="card__art" viewBox="0 0 480 272" aria-hidden="true">
    <path d="M345,0 L480,0 L480,272 L345,272 C270,200 270,72 345,0 Z" fill="#121212"/>
    <path d="M338,0 C262,72 262,200 338,272" fill="none" stroke="#c79a45" stroke-width="2"/>
  </svg>

  <div class="back__person">
    <h1 class="back__name">Henrike Mollberg</h1>
    <p class="back__role">Yoga &amp; Beckenbodentraining</p>
    <div class="back__rule"></div>
  </div>

  <ul class="contact-list">
    <li class="contact-list__item">
      <span class="contact-list__icon">
        <svg viewBox="0 0 24 24" aria-hidden="true"><path d="M6.6 10.8a15.1 15.1 0 0 0 6.6 6.6l2.2-2.2c.3-.3.7-.4 1-.2 1.1.4 2.3.6 3.6.6.6 0 1 .4 1 1V20c0 .6-.4 1-1 1A17 17 0 0 1 3 4c0-.6.4-1 1-1h3.5c.6 0 1 .4 1 1 0 1.3.2 2.5.6 3.6.1.3 0 .7-.2 1z"/></svg>
      </span>
      0176 - 4830915
    </li>
    <li class="contact-list__item">
      <span class="contact-list__icon">
        <svg viewBox="0 0 24 24" aria-hidden="true"><path d="M12 2a10 10 0 1 0 0 20 10 10 0 0 0 0-20zm6.9 6h-2.9a15.7 15.7 0 0 0-1.4-3.6A8 8 0 0 1 18.9 8zM12 4c.8 1.2 1.5 2.5 1.9 4h-3.8c.4-1.4 1.1-2.8 1.9-4zM4.3 14a8 8 0 0 1 0-4h3.4a16 16 0 0 0 0 4zm.8 2h2.9c.3 1.3.8 2.5 1.4 3.6A8 8 0 0 1 5.1 16zM8 8H5.1a8 8 0 0 1 4.3-3.6C8.8 5.5 8.3 6.7 8 8zm4 12c-.8-1.2-1.5-2.5-1.9-4h3.8c-.4 1.4-1.1 2.8-1.9 4zm2.3-6H9.7a14.6 14.6 0 0 1 0-4h4.6a14.6 14.6 0 0 1 0 4zm.3 5.6c.6-1.1 1.1-2.300 1.4-3.6h2.9a8 8 0 0 1-4.3 3.6zm1.7-5.6a16 16 0 0 0 0-4h3.4a8 8 0 0 1 0 4z"/></svg>
      </span>
      www.stille-im-atem.de
    </li>
    <li class="contact-list__item">
      <span class="contact-list__icon">
        <svg viewBox="0 0 24 24" aria-hidden="true"><path d="M3 5h18c.6 0 1 .4 1 1v.4l-10 6.2L2 6.4V6c0-.6.4-1 1-1zm-1 3.7 10 6.2 10-6.2V18c0 .6-.4 1-1 1H3c-.6 0-1-.4-1-1z"/></svg>
      </span>
      info@stille-im-atem.de
    </li>
  </ul>

  <p class="back__brand">Stille im Atem</p>
</section>

</body>
</html>
```